Valderons Business Card

Business card for philanthropic organization

Industry/Entity Type

Business

Contact Information for Business Card

Need a very ELEGANT, sober, embossed, formal business card... it should transmit CREDIBILITY. Not looking for a "fun card". would like white, grays or black designs.

Font styles to use
Script

Requirements
Must have
• Embossed look

```html
<!DOCTYPE html>
<html lang="en">
<head>
<meta charset="UTF-8">
<title>Valderons Business Card</title>
<link rel="stylesheet" href="https://fonts.googleapis.com/css2?family=Open+Sans:wght@400;600&display=swap">
<style>
  :root {
    --page-bg: #e9e9e7;
    --card-white: #ffffff;
    --silver-light: #fbfbfb;
    --silver-mid: #d9d9d9;
    --silver-dark: #a9a9a9;
    --ink: #3a3a3a;
    --ink-soft: #7a7a7a;
    --accent: #d98a1e;
    --shadow: rgba(0, 0, 0, 0.22);
  }
  * { box-sizing: border-box; margin: 0; padding: 0; }
  html, body {
    width: 1200px; height: 1000px; overflow: hidden;
    background: var(--page-bg);
    font-family: "Open Sans", Arial, sans-serif;
  }
  .canvas {
    position: relative; width: 1200px; height: 1000px;
  }
  .card {
    position: absolute; left: 250px; width: 700px; height: 400px;
    box-shadow: 0 10px 28px var(--shadow), 0 2px 4px rgba(0,0,0,0.12);
    overflow: hidden;
  }
  /* back face */
  .card--back {
    top: 60px;
    background: radial-gradient(ellipse at 50% 40%, var(--silver-light) 0%, var(--silver-mid) 60%, var(--silver-dark) 100%);
    display: flex; flex-direction: column; align-items: center; justify-content: center;
  }
  .emblem-mark {
    display: flex; align-items: center; gap: 14px;
    color: var(--ink); font-weight: 600; font-size: 40px; letter-spacing: 1px;
  }
  .emblem-mark__dot {
    width: 22px; height: 22px; border-radius: 50%; background: var(--ink);
  }
  .card--back .card__email {
    margin-top: 34px;
    font-size: 13px; letter-spacing: 4px; text-transform: uppercase; color: var(--ink);
  }
  /* front face */
  .card--front {
    top: 540px; display: flex; background: var(--card-white);
  }
  .card__identity {
    width: 44%; padding: 36px 0 0 34px; background: var(--card-white);
    display: flex; flex-direction: column;
  }
  .card__identity .emblem-mark {
    font-size: 20px; gap: 8px; margin-bottom: 34px;
  }
  .card__identity .emblem-mark__dot { width: 12px; height: 12px; }
  .card__name {
    color: var(--accent); font-weight: 600; font-size: 31px; line-height: 1.1;
  }
  .card__org, .card__role {
    color: var(--ink-soft); font-size: 24px; line-height: 1.2;
  }
  .card__contact {
    flex: 1;
    background: radial-gradient(ellipse at 45% 65%, var(--silver-light) 0%, var(--silver-mid) 55%, var(--silver-dark) 100%);
    padding: 26px 30px 0 0;
    text-align: right; color: var(--ink); font-size: 17px; line-height: 1.55;
    list-style: none;
  }
</style>
</head>
<body>
<main class="canvas">
  <section class="card card--back" aria-label="Card back">
    <div class="emblem-mark"><span class="emblem-mark__dot"></span>Valderons</div>
    <p class="card__email">msolanilla@postline.net</p>
  </section>

  <section class="card card--front" aria-label="Card front">
    <div class="card__identity">
      <div class="emblem-mark"><span class="emblem-mark__dot"></span>Valderons</div>
      <h1 class="card__name">Mateo Solanilla</h1>
      <p class="card__org">Dar Amin Valderons</p>
      <p class="card__role">Potentate 2017</p>
    </div>
    <ul class="card__contact">
      <li>0812-05517</li>
      <li>Panama, Republic of Panama</li>
      <li>+(507)-6123-4480</li>
      <li>msolanilla@postline.net</li>
    </ul>
  </section>
</main>
</body>
</html>
```